Business Card Design - Photographer

I am a landscape photographer and I require a business card design. 

I require two designs:
1)  a double sided business card
 and
b)  a single sided business card 

The single sided design can either be the same as the double sided (with just one side having all the information)....or it can be an entire new design. Its up to you.

My corporate colours are (CMYK):

Blue   69, 32, 0, 0
Grey  72,  64,  47,  31
Green  32,  2,  91,  0
Yellow   0, 19, 92, 0
Orange  0, 39, 75, 0

Colour space in final file should be in CMYK.

The details that need to be included on the card:

- Use the provided Logo
- Name: Wiktor Baranowski
- Email:   sales@vistalumeworks.com.au
- Website:    vistalumeworks.com.au
- Twitter:    twitter.com/vistalumeworks
- Facebook:   facebook.com/vistalumeworks
- Mobile  0417 539 662

Please use the attached template to design the logo to the specified size, including the marked bleed lines. I have also attached my logo in PNG (transparent background) and ai format for you to use.

The final file should be:
- Photoshop version with layers so I can edit the name/text etc. All non vector files should be high resolution at 1039 x 697 pixels at 300 dpi.

I also require a file as:
- Vector based PDF

Anyway questions please contact me.

Thank you

Industry/Entity Type

Landscape

Logo styles of interest
Pictorial/Combination Logo
Abstract Logo
Wordmark Logo
Lettermark Logo
Requirements
Must have
• The details that need to be included on the card:

- Use the provided Logo
- Name: Wiktor Baranowski
- Email: sales@vistalumeworks.com.au
- Website: vistalumeworks.com.au
- Twitter: twitter.com/vistalumeworks
- Facebook: facebook.com/vistalumeworks
- Mobile 0417 539 662

```html
<!DOCTYPE html>
<html lang="en">
<head>
<meta charset="utf-8">
<title>Vista Lume Works – Business Card</title>
<link rel="stylesheet" href="https://fonts.googleapis.com/css2?family=Cinzel:wght@400;600&display=swap">
<style>
  :root {
    --backdrop: #808184;
    --card: #ffffff;
    --ink: #3b3e4f;
    --blue: #3d92d0;
    --green: #b6d33e;
    --yellow: #ffc80f;
    --orange: #fba54b;
  }
  html, body {
    margin: 0;
    width: 1200px;
    height: 736px;
    overflow: hidden;
    background: var(--backdrop);
  }
  .card {
    position: absolute;
    left: 140px;
    top: 105px;
    width: 937px;
    height: 535px;
    background: var(--card);
    border-radius: 38px;
    overflow: hidden;
    font-family: "Cinzel", serif;
    color: var(--ink);
  }
  .foliage-art {
    position: absolute;
    left: 0;
    top: 0;
    width: 295px;
    height: 535px;
    background: linear-gradient(160deg, var(--green) 0%, var(--blue) 30%, var(--ink) 55%, var(--yellow) 75%, var(--orange) 100%);
    opacity: 0.85;
  }
  .identity {
    position: absolute;
    left: 418px;
    top: 42px;
    width: 444px;
    text-align: center;
  }
  .brand-dot {
    display: block;
    width: 154px;
    height: 154px;
    margin: 0 auto;
    border-radius: 50%;
    background: var(--ink);
  }
  .brand-name {
    margin: 22px 0 0;
    font-size: 40px;
    font-weight: 600;
    letter-spacing: 0;
    line-height: 1;
    white-space: nowrap;
  }
  .brand-rule {
    height: 2px;
    background: var(--ink);
    margin: 7px 10px 0;
  }
  .tagline {
    margin: 6px 0 0;
    font-size: 16px;
    font-weight: 600;
    letter-spacing: 3.5px;
    line-height: 1.2;
  }
  .contacts {
    list-style: none;
    margin: 24px 0 0;
    padding: 0;
    font-size: 21px;
    line-height: 35px;
    white-space: nowrap;
  }
  .contacts .key {
    color: var(--blue);
  }
</style>
</head>
<body>
  <div class="card">
    <div class="foliage-art" role="img" aria-label="Decorative tree branch with colourful leaves in blue, green, yellow, orange and grey"></div>
    <div class="identity">
      <span class="brand-dot"></span>
      <h1 class="brand-name">VISTA LUME WORKS</h1>
      <div class="brand-rule"></div>
      <p class="tagline">FINE ART PHOTOGRAPHY</p>
      <ul class="contacts">
        <li><span class="key">E</span> : SALES@VISTALUMEWORKS.COM.AU</li>
        <li><span class="key">W</span> : VISTALUMEWORKS.COM.AU</li>
        <li><span class="key">T</span> : CHIRPLANE.COM/VISTALUMEWORKS</li>
        <li><span class="key">F</span> : CIRCLEPAGE.COM/VISTALUMEWORKS</li>
        <li><span class="key">M</span> : 0417 539 662</li>
      </ul>
    </div>
  </div>
</body>
</html>
```